Business Card Design

We like to use greens as you will see in our logo (but not TOO much green). We are a Dental Clinic in a somewhat eccentric community. We do not like the dated sharp designs which we see many dentists use. We're looking for something bright and fresh while still maintaining the integrity of the profession. Elegance is not necessarily what we are going for... we need for the design to be "mature" but also up-lifting.

See our logo.
Updates

Project Deadline Extended
Reason: We have 5 designs which we like. But we'd like to see a few more before committing to a design.

Project Deadline Extended
Reason: We are awaiting revisions to this project. We are still welcoming designs while we wait to see if designers are able to provide to us the revisions we require in order to proceed with a selection.

Target Market(s)

Younger families - ages late 20's to early 40's

Industry/Entity Type

Business

Contact Information for Business Card

Corwel T. Banfry DDS 2730 W. Halvert Rd. Ste. 7 Royal Oak, MI 48391 (248)555-0174 FX (248)555-0189 info@BrightwellDentalCareMi.com BrigthwellDentalCareMi.com on the back of the card we need an appointment reminder (For____ Date___ Time____) with "If you are unable to keep your appointment, kindly give 48 hours notice" at the bottom. No use of teeth in the design. DOUBLE SIDED DESIGN

Requirements
Should not have
• The use of pictures of teeth

```html
<!DOCTYPE html>
<html lang="en">
<head>
<meta charset="utf-8">
<title>Brightwell Dental Care – Business Card</title>
<link rel="stylesheet" href="https://fonts.googleapis.com/css2?family=Arimo:ital,wght@0,400;0,700;1,400&family=Cinzel:wght@500&display=swap">
<style>
  :root {
    --green-deep: #1f6b36;
    --green-brand: #23703a;
    --green-leaf: #6cbf3f;
    --ink: #2b2b2b;
    --paper: #ffffff;
    --backdrop: #e8e6e2;
    --rule: #8a8a8a;
  }
  * { box-sizing: border-box; margin: 0; padding: 0; }
  html, body { width: 1200px; height: 1160px; overflow: hidden; }
  body {
    background: var(--backdrop);
    font-family: "Arimo", Arial, sans-serif;
    color: var(--ink);
    position: relative;
  }
  .card {
    position: absolute;
    background: var(--paper);
    box-shadow: 0 4px 14px rgba(0,0,0,.18);
    overflow: hidden;
  }

  /* Front */
  .card-front { left: 42px; top: 34px; width: 909px; height: 518px; }
  .front-brand {
    position: absolute; left: 0; right: 0; top: 120px;
    display: flex; align-items: center; justify-content: center; gap: 18px;
  }
  .brand-dot { width: 40px; height: 40px; border-radius: 50%; background: var(--green-leaf); }
  .brand-name {
    font-weight: 700; font-size: 58px; color: var(--green-brand); letter-spacing: .5px;
  }
  .front-band {
    position: absolute; left: 0; bottom: 0; width: 100%; height: 186px;
    background: var(--green-deep); color: var(--paper);
  }
  .person { position: absolute; left: 31px; top: 14px; }
  .person-name { font-weight: 700; font-size: 33px; }
  .person-title { font-weight: 700; font-size: 21px; margin-top: 12px; }
  .address { position: absolute; left: 31px; top: 112px; font-size: 22px; line-height: 34px; }
  .address .line2 { padding-left: 20px; }
  .contacts { position: absolute; left: 511px; top: 10px; list-style: none; font-size: 22px; }
  .contacts li { display: flex; align-items: center; gap: 10px; height: 42px; }
  .contacts li.small { font-size: 20px; }
  .contacts svg { width: 18px; height: 18px; flex: none; }
  .icon { fill: none; stroke: var(--paper); stroke-width: 2; }
  .icon-fill { fill: var(--paper); }

  /* Back */
  .card-back { left: 247px; top: 595px; width: 913px; height: 521px; }
  .back-brand {
    position: absolute; left: 75px; top: 60px;
    display: flex; align-items: center; gap: 12px;
  }
  .back-brand .brand-dot { width: 26px; height: 26px; }
  .back-brand .brand-name { font-size: 36px; }
  .appt-title {
    position: absolute; left: 78px; top: 172px;
    font-family: "Cinzel", Georgia, serif; font-weight: 500; font-size: 31px;
    color: var(--green-brand); letter-spacing: 1px;
  }
  .field { position: absolute; font-size: 24px; display: flex; align-items: baseline; }
  .dots { border-bottom: 2px dotted var(--rule); margin: 0 8px; height: 1px; align-self: flex-end; margin-bottom: 6px; }
  .field-name { left: 80px; top: 245px; }
  .field-name .dots { width: 505px; }
  .field-date { left: 80px; top: 312px; }
  .field-date .date-dots { width: 165px; margin-right: 20px; }
  .field-date .time-dots { width: 155px; }
  .field-next { left: 80px; top: 376px; align-items: center; }
  .slot { width: 162px; height: 34px; border: 2px solid #555; border-radius: 3px; margin-left: 20px; }
  .slot + .slot { margin-left: 39px; }
  .days { position: absolute; right: 28px; top: 75px; list-style: none; }
  .days li {
    display: flex; justify-content: flex-end; align-items: center; gap: 14px;
    font-weight: 700; font-size: 24px; height: 31px; margin-bottom: 31px;
  }
  .days li:nth-child(4) { margin-top: 2px; }
  .days li:nth-child(5) { margin-bottom: 25px; }
  .day-box { width: 56px; height: 31px; border: 2px solid #555; border-radius: 3px; }
  .notice {
    position: absolute; left: 75px; top: 448px; font-style: italic; font-size: 24px;
  }
  .back-band { position: absolute; left: 0; bottom: 0; width: 100%; height: 12px; background: var(--green-deep); }
</style>
</head>
<body>

<section class="card card-front" aria-label="Business card front">
  <div class="front-brand">
    <span class="brand-dot"></span>
    <span class="brand-name">Brightwell Dental Care</span>
  </div>
  <div class="front-band">
    <div class="person">
      <div class="person-name">Corwel T. Banfry</div>
      <div class="person-title">DDS</div>
    </div>
    <div class="address">
      <div><svg width="14" height="18" viewBox="0 0 14 18"><path class="icon-fill" d="M7 0a7 7 0 0 0-7 7c0 5 7 11 7 11s7-6 7-11a7 7 0 0 0-7-7zm0 10a3 3 0 1 1 0-6 3 3 0 0 1 0 6z"/></svg> 2730 W. Halvert Rd.</div>
      <div class="line2">Ste. 7 Royal Oak, MI 48391</div>
    </div>
    <ul class="contacts">
      <li><svg viewBox="0 0 18 18"><circle class="icon" cx="9" cy="9" r="8"/><path class="icon-fill" d="M6 4l2 2-1 1.5c.6 1.4 1.6 2.4 3 3L11.5 9.5l2 2-1.5 1.8C8 13 5 10 4.7 5.5z"/></svg>(248) 555-0174</li>
      <li><svg viewBox="0 0 18 18"><rect class="icon-fill" x="2" y="7" width="14" height="8" rx="1"/><rect class="icon" x="5" y="2" width="8" height="5"/></svg>(248) 555-0189</li>
      <li><svg viewBox="0 0 18 18"><rect class="icon" x="1.5" y="4" width="15" height="11" rx="1"/><path class="icon" d="M1.5 5l7.5 6 7.5-6"/></svg>info@BrightwellDentalCareMi.com</li>
      <li class="small"><svg viewBox="0 0 18 18"><circle class="icon" cx="9" cy="9" r="7.5"/><ellipse class="icon" cx="9" cy="9" rx="3.5" ry="7.5"/><path class="icon" d="M1.5 9h15"/></svg>BrigthwellDentalCareMi.com</li>
    </ul>
  </div>
</section>

<section class="card card-back" aria-label="Appointment card back">
  <div class="back-brand">
    <span class="brand-dot"></span>
    <span class="brand-name">Brightwell Dental Care</span>
  </div>
  <h2 class="appt-title">YOUR APPOINTMENT</h2>
  <div class="field field-name">Name :<span class="dots"></span></div>
  <div class="field field-date">Date :<span class="dots date-dots"></span>Time :<span class="dots time-dots"></span>am / pm</div>
  <div class="field field-next">Next Appointment<span class="slot"></span><span class="slot"></span></div>
  <ul class="days">
    <li>MON<span class="day-box"></span></li>
    <li>TUE<span class="day-box"></span></li>
    <li>WED<span class="day-box"></span></li>
    <li>THU<span class="day-box"></span></li>
    <li>FRI<span class="day-box"></span></li>
    <li>SAT<span class="day-box"></span></li>
  </ul>
  <p class="notice">If you are unable to keep your appointment, kindly give 48 hours notice</p>
  <div class="back-band"></div>
</section>

</body>
</html>
```